Property management company looking for modern card design

We at Blue Heron Partners provides property management services for its residential and commercial properties, with expertise in all categories of multifamily, industrial and office projects throughout California.

We need a business card design that is professional and modern designed business card. In our field, clients get hundreds of business cards, we would like our card to stand out.

Please avoid small print.

Target Market(s)

Professionals and high end clients

Industry/Entity Type

Financial Planning

Contact Information for Business Card

Company Name: Blue Heron Partners, Name, email, license #, phone number, website blueheronpartners.com

Font styles to use
Sans Serif

Requirements
Must have
• The card design needs to be adaptable because there is a possibly we will be expanding into different sectors other than real estate. The card design should be focused on financial planning and asset management.
Nice to have
• Modern and simple business card. Eye catching. Non-standard size/shaped cards would be great.
• blueheronpartners.com
Should not have
• Too many bright color or any pictures or shapes of real estate stuff.

```html
<!DOCTYPE html>
<html lang="en">
<head>
<meta charset="utf-8">
<title>Blue Heron Partners — Business Card</title>
<link rel="stylesheet" href="https://fonts.googleapis.com/css2?family=Cabin:wght@400;600&display=swap">
<style>
  :root {
    --backdrop: #869b97;
    --olive: #8e7b3d;
    --navy: #16232b;
    --wine: #6b0007;
    --signal-red: #e3001b;
    --brand-red: #d0021b;
    --white: #ffffff;
  }
  html, body {
    margin: 0;
    padding: 0;
    width: 1200px;
    height: 1200px;
    overflow: hidden;
    background: var(--backdrop);
  }
  .canvas {
    position: relative;
    width: 1200px;
    height: 1200px;
  }
  .card {
    position: absolute;
    left: 244px;
    width: 666px;
    height: 380px;
    display: block;
  }
  .card--front { top: 146px; }
  .card--back  { top: 636px; }
  .card__frame { fill: var(--wine); }
  .card__face--front { fill: var(--olive); }
  .card__face--back  { fill: var(--navy); }
  .card__edge {
    fill: none;
    stroke: var(--signal-red);
    stroke-width: 3;
  }
  .brand__mark { fill: var(--wine); }
  .brand__name {
    font-family: "Cabin", sans-serif;
    font-weight: 600;
    font-size: 44px;
    letter-spacing: 3px;
    fill: var(--brand-red);
  }
  .contact__pill { fill: var(--wine); }
  .contact__label {
    font-family: "Cabin", sans-serif;
    font-weight: 400;
    font-size: 36px;
    fill: var(--white);
  }
  .contact__icon-fill { fill: var(--navy); }
  .contact__icon-line {
    fill: none;
    stroke: var(--navy);
    stroke-width: 2.5;
    stroke-linejoin: round;
  }
</style>
</head>
<body>
<main class="canvas">

  <svg class="card card--front" viewBox="0 0 832 474" aria-label="Front of card">
    <rect class="card__frame" x="0" y="0" width="832" height="474"/>
    <path class="card__face--front"
          d="M0 100 Q0 0 100 0 L565 0 Q790 15 832 78 L832 394 Q832 474 752 474 L255 474 Q40 458 0 382 Z"/>
    <path class="card__edge" d="M565 0 Q790 15 832 78"/>
    <path class="card__edge" d="M255 474 Q40 458 0 382"/>

    <g class="brand">
      <circle class="brand__mark" cx="427" cy="167" r="86"/>
      <text class="brand__name" x="416" y="312" text-anchor="middle">Blue Heron Partners</text>
    </g>
  </svg>

  <svg class="card card--back" viewBox="0 0 832 478" aria-label="Back of card">
    <rect class="card__frame" x="0" y="0" width="832" height="478"/>
    <path class="card__face--back"
          d="M0 100 Q0 0 100 0 L580 0 Q790 15 832 82 L832 398 Q832 478 752 478 L255 478 Q40 462 0 386 Z"/>
    <path class="card__edge" d="M580 0 Q790 15 832 82"/>
    <path class="card__edge" d="M255 478 Q40 462 0 386"/>

    <g class="contact contact--name">
      <rect class="contact__pill" x="125" y="48" width="602" height="78" rx="39"/>
      <circle class="contact__icon-fill" cx="241" cy="83" r="30"/>
      <circle cx="241" cy="75" r="8" fill="var(--wine)"/>
      <path d="M228 97 Q241 80 254 97 Z" fill="var(--wine)"/>
      <text class="contact__label" x="427" y="96" text-anchor="middle">Individual Name</text>
    </g>

    <g class="contact contact--phone">
      <rect class="contact__pill" x="125" y="153" width="602" height="78" rx="39"/>
      <path class="contact__icon-fill"
            d="M228 167 L238 165 L244 178 L237 184 Q243 198 258 205 L264 198 L276 204 L274 214 Q266 220 254 214 Q230 202 222 180 Q220 172 228 167 Z"/>
      <text class="contact__label" x="427" y="201" text-anchor="middle">Phone Number</text>
    </g>

    <g class="contact contact--email">
      <rect class="contact__pill" x="125" y="258" width="602" height="78" rx="39"/>
      <path class="contact__icon-line" d="M230 293 L254 276 L278 293 L278 318 L230 318 Z"/>
      <path class="contact__icon-line" d="M230 293 L254 308 L278 293 M230 318 L248 304 M278 318 L260 304"/>
      <text class="contact__label" x="427" y="307" text-anchor="middle">E-mail</text>
    </g>

    <g class="contact contact--web">
      <rect class="contact__pill" x="125" y="356" width="602" height="78" rx="39"/>
      <circle class="contact__icon-line" cx="254" cy="394" r="22"/>
      <ellipse class="contact__icon-line" cx="254" cy="394" rx="10" ry="22"/>
      <path class="contact__icon-line" d="M232 394 L276 394 M236 382 L272 382 M236 406 L272 406 M254 372 L254 416"/>
      <text class="contact__label" x="427" y="404" text-anchor="middle">Website</text>
    </g>
  </svg>

</main>
</body>
</html>
```